Business card design for new eCommerce site focusing on integrity and strong businsess tactics

We need a business card that will stand out and be memorable. Something with color that matches our company logo colors. Think high end version of Pactivo. There are 2 logos provided. The parent company is called Amber Ledge Partners and we are presenting a new and very exciting eCommerce site called BrightHarborTrade.example.

Target Market(s)

Our target markets are in the Activities, Food and Beverage, Health and Beauty

Industry/Entity Type

Marketing

Contact Information for Business Card

We have 4 members that need cards...I will provide all info to the winner of the design contest
Business Address is
4870 West 63rd Avenue, Suite C207
Phoenix AZ 85731

Font styles to use
Serif
Sans Serif

Colors

Designer to choose colors to be used in the design.

Requirements
Must have
• The card must be memorable...should be unique in design but must exude integrity and be playful .
• I have provided several colors or our parent company...please feel free to use which ever
Nice to have
• I will leave this up to you. Feel free to use other images of your choosing that wraps around our client.....Activities, Dining, Health, Beauty
Should not have
• just dont be boring

```html
<!DOCTYPE html>
<html lang="en">
<head>
<meta charset="utf-8">
<title>Amber Ledge Partners – Business Card</title>
<link href="https://fonts.googleapis.com/css2?family=Montserrat:wght@400;500;600;700&display=swap" rel="stylesheet">
<style>
  :root {
    --page-bg: #2a2a2c;
    --card-bg: #1c1c1e;
    --green: #7cc242;
    --blue: #2f86c6;
    --white: #f2f2f2;
    --muted: #d8d8d8;
  }
  * { box-sizing: border-box; margin: 0; padding: 0; }
  html, body {
    width: 1200px; height: 930px; overflow: hidden;
    background: var(--page-bg);
    font-family: "Montserrat", sans-serif;
  }
  .card {
    position: absolute; left: 250px;
    width: 700px; height: 400px;
    background: var(--card-bg);
    border-radius: 18px; overflow: hidden;
    box-shadow: 0 14px 30px rgba(0,0,0,.45);
  }
  .card--front { top: 45px; }
  .card--back { top: 485px; }

  /* Front */
  .brand-lockup {
    position: absolute; left: 0; right: 0; top: 140px;
    display: flex; justify-content: center; align-items: center; gap: 18px;
  }
  .brand-mark { width: 22px; height: 22px; border-radius: 50%; background: var(--blue); flex: none; }
  .brand-name { font-size: 34px; font-weight: 600; color: var(--green); letter-spacing: -0.5px; line-height: 1; }
  .brand-tagline { margin-top: 8px; font-size: 15px; font-weight: 500; color: var(--white); letter-spacing: 1px; }
  .front-url {
    position: absolute; left: 0; right: 0; bottom: 70px; text-align: center;
    font-size: 14px; color: var(--white); letter-spacing: 1px;
  }
  .front-url span { color: var(--green); }

  /* Back */
  .company {
    position: absolute; left: 50px; top: 110px; width: 300px; text-align: center;
  }
  .company-mark { width: 60px; height: 60px; border: 5px solid var(--green); border-radius: 50%; margin: 0 auto 18px; }
  .company-name { font-size: 32px; font-weight: 700; color: var(--green); line-height: 1.05; }
  .divider { position: absolute; left: 375px; top: 60px; width: 1.5px; height: 200px; background: var(--blue); }
  .contact { position: absolute; left: 400px; top: 62px; color: var(--white); }
  .person-name { font-size: 20px; font-weight: 700; color: var(--green); }
  .person-title { font-size: 16px; margin-bottom: 14px; }
  .contact-row { display: flex; align-items: center; gap: 10px; font-size: 13px; line-height: 22px; color: var(--muted); }
  .contact-row svg { width: 13px; height: 13px; flex: none; }
  .contact-address { font-size: 13px; line-height: 20px; color: var(--muted); margin-top: 6px; }
  .wave { position: absolute; left: 0; bottom: 0; width: 700px; height: 400px; }
</style>
</head>
<body>

<section class="card card--front" aria-label="Card front">
  <div class="brand-lockup">
    <div class="brand-mark"></div>
    <div>
      <div class="brand-name">BrightHarborTrade.example</div>
      <div class="brand-tagline">Outings-Food-Wellness-Style</div>
    </div>
  </div>
  <p class="front-url">www.<span>amberledgepartners</span>.example</p>
</section>

<section class="card card--back" aria-label="Card back">
  <div class="company">
    <div class="company-mark"></div>
    <div class="company-name">Amber Ledge Partners</div>
  </div>
  <div class="divider"></div>
  <div class="contact">
    <div class="person-name">Daniel Reyes</div>
    <div class="person-title">Founder</div>
    <div class="contact-row">
      <svg viewBox="0 0 12 12"><rect x="3" y="0.5" width="6" height="11" rx="1" fill="none" stroke="#f2f2f2"/></svg>
      0413 555 019
    </div>
    <div class="contact-row">
      <svg viewBox="0 0 12 12"><rect x="0.5" y="2" width="11" height="8" fill="#f2f2f2"/><path d="M1 2.5 6 7 11 2.5" fill="none" stroke="#1c1c1e"/></svg>
      info@brightharbortrade.example
    </div>
    <div class="contact-row">
      <svg viewBox="0 0 12 12"><circle cx="5" cy="5" r="3.5" fill="none" stroke="#f2f2f2" stroke-width="1.5"/><path d="M7.5 7.5 11 11" stroke="#f2f2f2" stroke-width="1.5"/></svg>
      www.brightharbortrade.example
    </div>
    <p class="contact-address">4870 West 63rd Avenue,<br>Suite C207 Phoenix AZ 85731</p>
  </div>
  <svg class="wave" viewBox="0 0 700 400" aria-hidden="true">
    <path d="M0 380 C140 300 300 320 450 300 C560 285 640 262 700 240 L700 400 L0 400 Z" fill="var(--green)"/>
    <path d="M0 392 C140 312 300 330 450 310 C560 296 640 272 700 250 L700 400 L0 400 Z" fill="var(--card-bg)"/>
    <path d="M0 398 C140 322 300 338 450 318 C560 304 640 282 700 260 L700 400 L0 400 Z" fill="var(--blue)"/>
  </svg>
</section>

</body>
</html>
```